Web design

We need the design for the logo and website for a women fashion website. No coding required. The colors used should be neutral (maybe with a light touch of color), the style should be modern, slightly luxurious, not too crowded. The target market is young professionals who love trendy clothes.
Updates

Need extra days to review

Target Market(s)

Young professionals

Industry/Entity Type

Apparel

Number of Pages Required

5+ page

Font styles to use
Sans Serif
Other font styles liked:
• Montserrat, Engravers Gothic, Benton Sans, gotham-book

Colors

Designer to choose colors to be used in the design.

```html
<!DOCTYPE html>
<html lang="en">
<head>
<meta charset="utf-8">
<title>LUNE — Review &amp; Payment</title>
<link href="https://fonts.googleapis.com/css2?family=Jost:wght@400;500&family=Inter:wght@400;500&display=swap" rel="stylesheet">
<style>
  :root{
    --ink:#1f1d2b;
    --gold:#d4a010;
    --gold-soft:#e9bd45;
    --muted:#c9c9c9;
    --line:#e6e6e6;
    --panel:#f5f5f5;
    --footer:#f4f3f1;
    --blush:#fde7dd;
    --sale:#e8392f;
    --blue:#1592d6;
  }
  *{box-sizing:border-box;margin:0;padding:0}
  html,body{width:1200px;height:1171px;overflow:hidden;background:#fff}
  body{position:relative;font-family:'Jost',sans-serif;color:var(--ink)}
  .abs{position:absolute}
  .header{position:absolute;left:0;top:0;width:1200px;height:76px;border-bottom:1px solid var(--line)}
  .nav a{position:absolute;top:28px;font-family:'Inter',sans-serif;font-size:14px;color:var(--ink);text-decoration:none}
  .nav .sale{color:var(--sale)}
  .brand{position:absolute;color:var(--ink);font-weight:500;white-space:nowrap}
  .header .brand{left:532px;top:18px;width:136px;text-align:center;font-size:31px;letter-spacing:1px}
  .tools{position:absolute;top:26px}
  .lang{font-family:'Inter',sans-serif;font-size:11px}
  .badge{position:absolute;left:1086px;top:37px;width:12px;height:12px;border-radius:50%;background:var(--gold);color:#fff;font-size:8px;text-align:center;line-height:12px}
  .step-line{position:absolute;top:150px;height:1px}
  .step{position:absolute;top:130px;width:40px;height:40px;border-radius:50%;background:var(--gold);color:#fff;font-family:'Inter',sans-serif;font-size:22px;text-align:center;line-height:40px}
  .step.todo{background:#dedede}
  .step-label{position:absolute;top:187px;width:200px;text-align:center;font-family:'Inter',sans-serif;font-size:14px;font-weight:500}
  .step-label.todo{color:var(--muted)}
  .title{left:161px;top:282px;font-size:21px;font-weight:500;letter-spacing:.6px}
  .rule{position:absolute;top:319px;height:1px}
  .cart{position:absolute;left:162px;top:349px;width:869px;height:317px;background:var(--panel)}
  .row{position:absolute;left:0;width:869px;background:#fff}
  .row .cell{position:absolute;top:0;height:100%;border-right:1px solid var(--line)}
  .th{position:absolute;top:16px;font-size:12.5px;font-weight:500;letter-spacing:.8px;transform:translateX(-50%)}
  .thumb{position:absolute;left:9px;width:46px;height:58px;background:linear-gradient(160deg,#d9c7b4,#a88a72)}
  .pname{position:absolute;left:67px;top:15px;font-family:'Inter',sans-serif;font-size:15px}
  .dot{position:absolute;left:67px;top:40px;width:15px;height:15px;border-radius:50%}
  .size{position:absolute;left:272px;width:138px;top:41px;text-align:center;font-size:10px;letter-spacing:.2px;color:#444}
  .qty{position:absolute;left:447px;top:24px;display:flex;border:1px solid #cfcfcf;background:#fff}
  .qty span{width:31px;height:30px;display:flex;align-items:center;justify-content:center;font-family:'Inter',sans-serif;font-size:12px}
  .qty .op{font-size:17px;font-weight:300}
  .qty span+span{border-left:1px solid #cfcfcf}
  .price{position:absolute;top:30px;font-family:'Inter',sans-serif;font-size:15px;transform:translateX(-50%)}
  .remove{position:absolute;left:814px;top:29px}
  .total{position:absolute;right:99px;top:284px;font-family:'Inter',sans-serif;font-size:17px;font-weight:500}
  .total small{font-size:9px;font-weight:400}
  .order{position:absolute;left:480px;top:701px;width:240px;height:51px;background:var(--blush);display:flex;align-items:center;justify-content:center;font-size:16px;font-weight:500;letter-spacing:.8px}
  .footer{position:absolute;left:0;top:833px;width:1200px;height:338px;background:var(--footer)}
  .footer .brand{left:101px;top:82px;font-size:50px;letter-spacing:1px}
  .fhead{position:absolute;font-size:16px;font-weight:500;letter-spacing:.8px}
  .flink{position:absolute;font-size:14px;color:#333;letter-spacing:.3px}
  .social{position:absolute;top:177px;width:32px;height:32px;border:1px solid var(--ink);border-radius:50%}
  .fdiv{position:absolute;left:111px;top:269px;width:977px;height:1px;background:#d8d8d8}
  .legal{position:absolute;left:0;width:1200px;top:292px;text-align:center;font-size:14px;color:#333}
</style>
</head>
<body>

<header class="header">
  <nav class="nav">
    <a style="left:99px">Latest Arrivals</a>
    <a style="left:217px">Clothes &#8964;</a>
    <a style="left:308px">LUNE Club</a>
    <a class="sale" style="left:412px">On Sale</a>
  </nav>
  <div class="brand">LUNE</div>
  <svg class="tools" style="left:918px" width="18" height="18" viewBox="0 0 18 18" fill="none" stroke="#1f1d2b" stroke-width="1.5"><circle cx="8" cy="8" r="6"/><path d="M12.5 12.5l4 4"/></svg>
  <div class="tools lang" style="left:963px;top:32px">ENG &#8964;</div>
  <svg class="tools" style="left:1009px;top:27px" width="24" height="22" viewBox="0 0 24 22" fill="none" stroke="#1f1d2b" stroke-width="1.6"><path d="M12 20S2 13.5 2 7a5 5 0 0 1 10-1 5 5 0 0 1 10 1c0 6.5-10 13-10 13z"/></svg>
  <svg class="tools" style="left:1042px" width="22" height="24" viewBox="0 0 22 24" fill="none" stroke="#1f1d2b" stroke-width="1.6"><circle cx="11" cy="7" r="5"/><path d="M1 23c0-6 4.5-9 10-9s10 3 10 9"/></svg>
  <svg class="tools" style="left:1074px" width="20" height="24" viewBox="0 0 20 24" fill="none" stroke="#1f1d2b" stroke-width="1.6"><path d="M2 8h16l-1 15H3z"/><path d="M6 8V5a4 4 0 0 1 8 0v3"/></svg>
  <div class="badge">0</div>
</header>

<div class="step-line" style="left:226px;width:232px;background:var(--gold)"></div>
<div class="step-line" style="left:478px;width:239px;background:var(--gold)"></div>
<div class="step-line" style="left:737px;width:229px;background:#dedede"></div>
<div class="step" style="left:186px">1</div>
<div class="step" style="left:438px">2</div>
<div class="step" style="left:697px">3</div>
<div class="step todo" style="left:946px">4</div>
<div class="step-label" style="left:106px">REVIEW</div>
<div class="step-label" style="left:358px">SHIPPING DETAILS</div>
<div class="step-label" style="left:617px">PAYMENT</div>
<div class="step-label todo" style="left:866px">CONFIRMATION</div>

<h1 class="abs title">REVIEW &amp; PAYMENT</h1>
<div class="rule" style="left:163px;width:798px;background:#d6d6d6"></div>
<div class="rule" style="left:163px;width:283px;background:var(--gold-soft)"></div>

<section class="cart">
  <div class="th" style="left:147px">PRODUCT NAME</div>
  <div class="th" style="left:340px">SIZE</div>
  <div class="th" style="left:499px">QUANTITY</div>
  <div class="th" style="left:645px">UNIT PRICE</div>
  <div class="th" style="left:787px">SUBTOTAL</div>

  <div class="row" style="top:46px;height:74px;border-bottom:1px solid var(--line)">
    <div class="cell" style="left:0;width:272px"></div><div class="cell" style="left:272px;width:138px"></div><div class="cell" style="left:410px;width:161px"></div><div class="cell" style="left:571px;width:151px"></div>
    <div class="thumb" style="top:9px" role="img" aria-label="Product photo of a white lace lingerie set"></div>
    <div class="pname">The standard Lorem</div>
    <div class="dot" style="background:var(--blue)"></div>
    <div class="size">L+(Regular cup)</div>
    <div class="qty"><span class="op">−</span><span>1</span><span class="op">+</span></div>
    <div class="price" style="left:645px">$221.99</div>
    <div class="price" style="left:777px">$221.99</div>
    <svg class="remove" width="20" height="20" viewBox="0 0 20 20" fill="none" stroke="#333"><circle cx="10" cy="10" r="9.3"/><path d="M7 7l6 6M13 7l-6 6"/></svg>
  </div>

  <div class="row" style="top:121px;height:75px;border-bottom:1px solid var(--line)">
    <div class="cell" style="left:0;width:272px"></div><div class="cell" style="left:272px;width:138px"></div><div class="cell" style="left:410px;width:161px"></div><div class="cell" style="left:571px;width:151px"></div>
    <div class="thumb" style="top:9px;left:12px;width:38px;background:linear-gradient(160deg,#ece4dc,#c9b6a6)" role="img" aria-label="Product photo of a cream knit lounge dress"></div>
    <div class="pname" style="left:66px">The standard Lorem Ipsum</div>
    <div class="dot" style="background:#2a2a2a"></div>
    <div class="size">L+(Regular cup)</div>
    <div class="qty"><span class="op">−</span><span>1</span><span class="op">+</span></div>
    <div class="price" style="left:645px">$221.99</div>
    <div class="price" style="left:777px">$221.99</div>
    <svg class="remove" width="20" height="20" viewBox="0 0 20 20" fill="none" stroke="#333"><circle cx="10" cy="10" r="9.3"/><path d="M7 7l6 6M13 7l-6 6"/></svg>
  </div>

  <div class="row" style="top:197px;height:76px">
    <div class="cell" style="left:0;width:272px"></div><div class="cell" style="left:272px;width:138px"></div><div class="cell" style="left:410px;width:161px"></div><div class="cell" style="left:571px;width:151px"></div>
    <div class="thumb" style="top:9px" role="img" aria-label="Product photo of a white lace lingerie set"></div>
    <div class="pname" style="left:66px">The standarpsum passag</div>
    <div class="dot" style="background:var(--blue)"></div>
    <div class="size">L+(Regular cup)</div>
    <div class="qty"><span class="op">−</span><span>1</span><span class="op">+</span></div>
    <div class="price" style="left:645px">$221.99</div>
    <div class="price" style="left:777px">$221.99</div>
    <svg class="remove" width="20" height="20" viewBox="0 0 20 20" fill="none" stroke="#333"><circle cx="10" cy="10" r="9.3"/><path d="M7 7l6 6M13 7l-6 6"/></svg>
  </div>

  <div class="total"><small>TOTAL: </small>$572.97</div>
</section>

<div class="order">PLACE YOUR ORDER</div>

<footer class="footer">
  <div class="brand">LUNE</div>

  <div class="fhead" style="left:445px;top:77px">HELP</div>
  <div class="flink" style="left:444px;top:116px">Terms &amp; Conditions</div>
  <div class="flink" style="left:444px;top:143px">Privacy Policy</div>
  <div class="flink" style="left:444px;top:169px">Returns/exchanges</div>
  <div class="flink" style="left:444px;top:196px">Delivery Information</div>
  <div class="flink" style="left:444px;top:223px">FAQ</div>

  <div class="fhead" style="left:737px;top:77px">SHOP</div>
  <div class="flink" style="left:736px;top:116px">Tops</div>
  <div class="flink" style="left:736px;top:143px">Bootoms</div>
  <div class="flink" style="left:736px;top:169px">Intimates</div>
  <div class="flink" style="left:736px;top:196px">Dresses</div>
  <div class="flink" style="left:736px;top:223px">Swim</div>

  <div class="fhead" style="left:961px;top:77px">CONTACT US</div>
  <svg class="abs" style="left:964px;top:107px" width="15" height="11" viewBox="0 0 15 11"><rect width="15" height="11" fill="#1f1d2b"/><path d="M0 0l7.5 6L15 0" fill="none" stroke="#f4f3f1" stroke-width="1.2"/></svg>
  <div class="flink" style="left:985px;top:102px">info@lune-studio.com</div>
  <div class="fhead" style="left:961px;top:146px">FOLLOW US</div>
  <div class="social" style="left:958px"></div>
  <div class="social" style="left:995px"></div>
  <div class="social" style="left:1031px"></div>
  <div class="social" style="left:1068px"></div>

  <div class="fdiv"></div>
  <div class="legal">Terms &amp; Conditions, Privacy Policy and @2021 followed by lune.</div>
</footer>

</body>
</html>
```